Corvane Capital Business Cards

These are professional business cards that are for my family office.
Put fake emails and phone numbers as of now until I finalize those components. This family office controls my families investments, assets, and future. The cards should be professional.
..
.
.
.
I just uploaded another variation of a logo I would like to see as a business card to I am inbeteen which logo to use

Target Market(s)

business

Industry/Entity Type

business

Contact Information for Business Card

Professional, wealth related, finance related.

Requirements
Must have
• Logo

```html
<!DOCTYPE html>
<html lang="en">
<head>
<meta charset="utf-8">
<title>Corvane Capital Business Cards</title>
<link rel="stylesheet" href="https://fonts.googleapis.com/css2?family=Montserrat:wght@400;600&display=swap">
<style>
  :root {
    --stage: #2b2b2d;
    --card: #1b2232;
    --card-edge: #232b3e;
    --emboss: #2c354c;
    --ink: #e6e8ee;
    --ink-soft: #b9bfcc;
    --rule: #8c93a3;
  }
  * { box-sizing: border-box; margin: 0; padding: 0; }
  html, body {
    width: 1200px; height: 875px; overflow: hidden;
    background: var(--stage);
  }
  .stage {
    width: 1200px; height: 875px;
    display: flex; flex-direction: column;
    align-items: center; justify-content: center; gap: 56px;
  }
  .card {
    width: 630px; height: 360px;
    background: var(--card);
    border: 1px solid var(--card-edge);
    border-radius: 22px;
    position: relative;
  }
  .card--back {
    display: flex; align-items: center; justify-content: center;
  }
  .wordmark-emboss {
    font-family: "Montserrat", sans-serif;
    font-weight: 600;
    font-size: 50px;
    color: var(--emboss);
    white-space: nowrap;
  }
  .card--front {
    display: flex; align-items: center;
    padding: 0 48px 0 50px;
  }
  .brand {
    width: 250px;
    display: flex; align-items: center; justify-content: center;
  }
  .brand__name {
    font-family: "Montserrat", sans-serif;
    font-weight: 600;
    font-size: 24px;
    color: var(--ink);
    white-space: nowrap;
  }
  .divider {
    width: 1px; height: 200px;
    background: var(--rule);
    margin: 0 26px 0 24px;
  }
  .details {
    font-family: "Montserrat", sans-serif;
    color: var(--ink-soft);
    font-size: 13px;
    line-height: 1.35;
  }
  .details__name {
    font-weight: 600; font-size: 21px; color: var(--ink-soft);
  }
  .details__role { margin-bottom: 20px; }
  .details__address { margin-bottom: 16px; }
  .contact { list-style: none; }
  .contact li {
    display: flex; align-items: center; gap: 10px;
    margin-bottom: 3px;
  }
  .contact svg { width: 12px; height: 12px; fill: none; stroke: var(--ink-soft); stroke-width: 1.6; }
</style>
</head>
<body>
<main class="stage">
  <section class="card card--back" aria-label="Card back">
    <p class="wordmark-emboss">Corvane Capital</p>
  </section>

  <section class="card card--front" aria-label="Card front">
    <div class="brand">
      <p class="brand__name">Corvane Capital</p>
    </div>
    <div class="divider"></div>
    <div class="details">
      <p class="details__name">Marcus Ellery</p>
      <p class="details__role">Owner</p>
      <p class="details__address">42 Harbor Crest Lane<br>Alden, NJ 07114 USA</p>
      <ul class="contact">
        <li>
          <svg viewBox="0 0 12 12"><path d="M2.5 1.5l2 2-1 1.5c.8 1.6 1.9 2.7 3.5 3.5l1.5-1 2 2-1.3 1.3C5.5 10.5 1.5 6.5 1.2 2.8z"/></svg>
          (555)014-2287
        </li>
        <li>
          <svg viewBox="0 0 12 12"><rect x="1" y="2.5" width="10" height="7"/><path d="M1 2.5l5 4 5-4"/></svg>
          info@corvanecapital.com
        </li>
        <li>
          <svg viewBox="0 0 12 12"><circle cx="6" cy="6" r="5"/><path d="M1 6h10M6 1c-2.5 3-2.5 7 0 10M6 1c2.5 3 2.5 7 0 10"/></svg>
          www.corvanecapital.com
        </li>
      </ul>
    </div>
  </section>
</main>
</body>
</html>
```